MRT Property - Business Cards

Looking for a business card & general letterhead, signage etc design for our new logo.

Colours:
000a20
0056a2
00b5ef
0088ce
68cef2

Fonts:
Poppins
Karla

Please keep look and feel of new brand - example in the zip package I sent.

```html
<!DOCTYPE html>
<html lang="en">
<head>
<meta charset="utf-8">
<title>MRT Property – Business Cards</title>
<link rel="stylesheet" href="https://fonts.googleapis.com/css2?family=Poppins:wght@300;400;500;700&display=swap">
<style>
  :root {
    --navy: #111629;
    --navy-deep: #000a20;
    --blue: #0056a2;
    --blue-mid: #0088ce;
    --cyan: #00b5ef;
    --sky: #68cef2;
    --indigo: #1b2456;
    --white: #ffffff;
    --stage: #e9ebef;
  }
  * { margin: 0; padding: 0; box-sizing: border-box; }
  html, body { width: 1200px; height: 711px; overflow: hidden; }
  body {
    background: var(--stage);
    font-family: "Poppins", sans-serif;
    display: flex;
    align-items: center;
    justify-content: center;
    gap: 40px;
  }
  .card {
    position: relative;
    width: 560px;
    height: 320px;
    background: var(--navy);
    border-radius: 4px;
    overflow: hidden;
    box-shadow: 0 10px 24px rgba(0, 10, 32, 0.25);
  }

  /* Back of card */
  .card-back__pattern {
    position: absolute;
    inset: 0;
    background: linear-gradient(30deg, var(--navy) 30%, var(--indigo) 65%, #1d3f8e 100%);
  }
  .card-back__brand {
    position: absolute;
    right: 52px;
    bottom: 118px;
    display: flex;
    align-items: center;
    gap: 6px;
    font-weight: 500;
    font-size: 14px;
    color: var(--cyan);
  }
  .brand-dot {
    width: 10px; height: 10px;
    border-radius: 50%;
    background: var(--cyan);
  }

  /* Front of card */
  .card-front__brand {
    position: absolute;
    left: 36px;
    top: 150px;
    display: flex;
    align-items: center;
    gap: 10px;
    font-weight: 700;
    font-size: 27px;
    line-height: 1;
    color: var(--blue);
    white-space: nowrap;
  }
  .card-front__brand .brand-dot {
    width: 22px; height: 22px;
    background: var(--blue-mid);
  }
  .card-front__divider {
    position: absolute;
    left: 290px;
    top: 40px;
    width: 1px;
    height: 190px;
    background: var(--blue);
  }
  .person {
    position: absolute;
    left: 320px;
    top: 44px;
  }
  .person__name {
    font-size: 27px;
    line-height: 1.1;
  }
  .person__first { font-weight: 700; color: var(--blue); }
  .person__last { font-weight: 300; color: var(--sky); }
  .person__role {
    margin-top: 2px;
    margin-left: 14px;
    font-size: 12px;
    font-weight: 500;
    color: var(--white);
  }
  .contacts {
    position: absolute;
    left: 334px;
    top: 128px;
    list-style: none;
  }
  .contacts__item {
    display: flex;
    align-items: center;
    gap: 8px;
    font-size: 11.5px;
    color: var(--white);
    line-height: 19px;
  }
  .contacts__icon { width: 12px; height: 12px; flex: none; }
  .address-band {
    position: absolute;
    left: 0; right: 0;
    top: 246px;
    height: 30px;
    background: var(--blue);
    display: flex;
    align-items: center;
    padding-left: 40px;
    font-size: 12.5px;
    color: var(--white);
    letter-spacing: 0.2px;
    white-space: nowrap;
  }
</style>
</head>
<body>

  <section class="card card-back" aria-label="Business card back">
    <div class="card-back__pattern" role="img" aria-label="Repeating brand symbol pattern in navy and blue, fading lighter toward the top right"></div>
    <div class="card-back__brand"><span class="brand-dot"></span>MRT Property</div>
  </section>

  <section class="card card-front" aria-label="Business card front">
    <div class="card-front__brand"><span class="brand-dot"></span>MRT Property</div>
    <div class="card-front__divider"></div>

    <div class="person">
      <p class="person__name"><span class="person__first">Callum</span> <span class="person__last">Reid</span></p>
      <p class="person__role">Director</p>
    </div>

    <ul class="contacts">
      <li class="contacts__item">
        <svg class="contacts__icon" viewBox="0 0 24 24" aria-hidden="true"><path fill="#68cef2" d="M6.6 10.8a15 15 0 0 0 6.6 6.6l2.2-2.2c.3-.3.7-.4 1-.2 1.1.4 2.3.6 3.6.6.6 0 1 .4 1 1V20c0 .6-.4 1-1 1A17 17 0 0 1 3 4c0-.6.4-1 1-1h3.5c.6 0 1 .4 1 1 0 1.3.2 2.5.6 3.6.1.3 0 .7-.2 1z"/></svg>
        +61 2 5550 0147
      </li>
      <li class="contacts__item">
        <svg class="contacts__icon" viewBox="0 0 24 24" aria-hidden="true"><circle cx="12" cy="12" r="10" fill="none" stroke="#68cef2" stroke-width="2"/><path d="M2 12h20M12 2c3 3 3 17 0 20M12 2c-3 3-3 17 0 20" fill="none" stroke="#68cef2" stroke-width="1.6"/></svg>
        www.mrtproperty.com.au
      </li>
      <li class="contacts__item">
        <svg class="contacts__icon" viewBox="0 0 24 24" aria-hidden="true"><rect x="2" y="5" width="20" height="14" rx="1.5" fill="none" stroke="#68cef2" stroke-width="2"/><path d="M2 6l10 7 10-7" fill="none" stroke="#68cef2" stroke-width="2"/></svg>
        info@mrtproperty.com.au
      </li>
    </ul>

    <div class="address-band">Suite 4.12, Level 4 18 Harbourline Way Westbrook NSW 2199</div>
  </section>

</body>
</html>
```